Eyecatching website design for commercial lighting business

This contest is all about the graphic design aspect. We need a striking website design for a commercial lighting company. We want something really eye catching to introduce people to our range of induction and LED lights which save businesses money on maintenance and electricity costs.

To be successful in this contest you will need to provide a design and pictures for the pages listed below.

We are using the platform velbrin.com.au and you can see the attached template which everything will be loaded into so we just need HTML files which we can upload and we can do everything else from Velbrin.

The final design should be strong and clean and use the colours and textures in the attached business card file.

Detailed requirements:

Please see attached screenshot of the website template, all we need is a fantastic graphic design and improvement/ incorporation of our logo for the following pages
Page Headings:
1. Home
About Us, Contact Us, snapshot of and link to Blog

Each of the below pages will have several paragraphs of text followed by a list of suitable products which is generated from our product catalogue.

2. Car Park Lighting
3. Educational Lighting
4. Hospitality Lighting
5. Office & Shop Lighting
6. Warehouse Lighting

Some of the website we have seen which are similar in nature are:
http://www.quorvanlamps.com.au/
http://www.tibrox.com/
http://www.gandowlumen.net/commercial-led
but we really want a modern, eye catching and memorable design

Some of the designs built on Velbrin that we like are:

http://www.pemberhollow.com.au/
http://www.marwickgoods.com.au/
http://www.kelmorabay.com.au/

I've also uploaded a couple of photos that we love. We'd like something similar for each industry.

Target Market(s)

Company Owners, Maintenance & Facilities Managers, Electrical Contractors

Industry/Entity Type

Electrical

Coding

Coded - Design and coding required

Number of Pages Required

5+ page

Font styles to use
Sans Serif

Colors
33a6d7
ec1f27

Requirements
Must have
• -Must scale to mobile
• -HTML coded files need to be provided (HTML Bootstrap)
Nice to have
• -Prefer incorporation of our logo into header bar
• -Design of 2-3 advertising banners which can be displayed on the home page
• -Prominent call to action button towards top of page 'Get a quote' or similar
• -Grid based design HTML Bootstrap

```html
<!DOCTYPE html>
<html lang="en">
<head>
<meta charset="utf-8">
<title>Harlow &amp; Finch Commercial Lighting</title>
<link rel="stylesheet" href="https://fonts.googleapis.com/css2?family=Oswald:wght@400;500;600&family=Open+Sans:wght@400;600;700&display=swap">
<style>
:root{
  --blue:#33a6d7;
  --red:#ec1f27;
  --dark:#1e1e1e;
  --darker:#141414;
  --grey-bg:#e9e9e9;
  --text:#555;
  --white:#fff;
  --line:#ddd;
}
*{box-sizing:border-box;margin:0;padding:0}
html,body{width:1200px;height:2524px;overflow:hidden}
body{background:var(--grey-bg);font-family:"Open Sans",sans-serif;color:var(--text);font-size:14px;line-height:1.6;position:relative}
.heading{font-family:"Oswald",sans-serif;text-transform:uppercase;letter-spacing:.5px}

/* header */
.site-header{position:absolute;top:0;left:0;width:1200px;height:80px;background:var(--dark);display:flex;align-items:center;padding:0 48px}
.brand{display:flex;align-items:center;gap:10px;color:var(--white);font-family:"Oswald",sans-serif;font-size:22px;font-weight:500;width:300px}
.brand-mark{width:26px;height:26px;background:var(--red)}
.main-nav{display:flex;margin-left:40px}
.main-nav a{color:var(--white);text-decoration:none;font-family:"Oswald",sans-serif;font-size:15px;padding:28px 22px;text-transform:uppercase}
.main-nav a.active{color:var(--red)}
.header-contact{margin-left:auto;color:var(--white);font-size:13px;line-height:1.5}
.header-contact div{display:flex;align-items:center;gap:8px}

/* hero */
.hero{position:absolute;top:80px;left:0;width:1200px;height:540px;background:linear-gradient(180deg,#5f6a70 0%,#b9c2c6 45%,#d6dadb 70%,#9aa2a6 100%)}
.hero-box{position:absolute;left:600px;top:250px;width:520px;height:240px;background:var(--blue);opacity:.95;color:var(--white);padding:36px 40px}
.hero-box h2{font-size:30px;font-weight:500;margin-bottom:12px}
.hero-box p{font-size:15px;margin-bottom:22px}
.btn{display:inline-block;font-family:"Oswald",sans-serif;text-transform:uppercase;font-size:14px;padding:10px 22px;text-decoration:none}
.btn-red{background:var(--red);color:var(--white)}
.btn-outline{border:1px solid var(--white);color:var(--white)}
.btn-text{color:var(--red);border:1px solid var(--red)}
.slider-dots{position:absolute;left:570px;top:522px;display:flex;gap:8px}
.slider-dots span{width:10px;height:10px;border-radius:50%;background:rgba(255,255,255,.6)}
.slider-dots span.on{background:var(--white)}

/* panels */
.panel{position:absolute;left:48px;width:1104px;background:var(--white)}
.welcome{top:650px;height:400px;padding:30px 40px}
.welcome .eyebrow{font-size:24px;color:#333}
.welcome h1{font-size:28px;color:var(--blue);font-weight:500;line-height:1.2;margin-bottom:18px}
.welcome p{margin-bottom:10px}
.welcome ul{list-style:none;margin-bottom:22px}
.welcome li{padding-left:20px;position:relative;margin-bottom:4px}
.welcome li::before{content:"";position:absolute;left:4px;top:9px;width:6px;height:6px;background:var(--blue);border-radius:50%}

.solutions{top:1090px;height:480px;padding:26px 40px}
.section-title{text-align:center;color:var(--blue);font-size:26px;font-weight:500}
.view-all{position:absolute;right:40px;top:76px;font-family:"Oswald",sans-serif;font-size:13px;color:#333}
.cards{display:flex;gap:40px;margin-top:40px}
.card{width:328px}
.card h3{font-size:20px;color:#333;font-weight:500;margin-bottom:10px}
.card-img{height:180px;margin-bottom:14px}
.card p{font-size:13px;margin-bottom:14px}

.media-row{top:1610px;height:520px;padding:30px 40px;display:flex;gap:40px}
.media-col{width:492px}
.media-col h2{color:var(--blue);font-size:28px;font-weight:500;border-bottom:2px solid var(--line);padding-bottom:8px;margin-bottom:22px}
.video{height:390px;position:relative;background:linear-gradient(180deg,#10151a 0%,#3d4a55 40%,#c7d3da 60%,#3b444b 100%)}
.video-bar{position:absolute;left:0;bottom:0;width:100%;height:36px;background:rgba(0,0,0,.75);display:flex;align-items:center;padding:0 12px;gap:12px}
.video-track{flex:1;height:4px;background:#555;position:relative}
.video-track::after{content:"";position:absolute;left:0;top:0;width:30%;height:4px;background:var(--red)}
.post{display:flex;gap:22px;margin-bottom:26px}
.post-img{width:230px;height:170px;position:relative;flex:none}
.date-tag{position:absolute;right:10px;top:10px;background:var(--red);color:var(--white);font-size:11px;padding:3px 8px;font-weight:700}
.post h3{font-size:18px;color:#333;font-weight:500;margin-bottom:8px}
.post p{font-size:13px}

/* footer */
.site-footer{position:absolute;top:2160px;left:0;width:1200px;height:320px;background:var(--dark);color:#bbb;padding:36px 48px;display:flex;gap:36px;font-size:12px}
.footer-col h4{color:var(--white);font-family:"Oswald",sans-serif;font-weight:400;font-size:15px;margin-bottom:12px;text-transform:uppercase}
.footer-col ul{list-style:none}
.footer-col li{margin-bottom:6px}
.social li{display:flex;align-items:center;gap:8px}
.social .dot{width:20px;height:20px;border-radius:50%;background:#555}
.payments{display:flex;gap:6px;margin-bottom:30px}
.payments span{width:40px;height:26px;background:#444;border-radius:3px}
.care{display:flex;align-items:center;gap:10px}
.care small{display:block;color:var(--white);font-family:"Oswald",sans-serif;font-size:14px}
.care strong{color:var(--white);font-family:"Oswald",sans-serif;font-size:30px;font-weight:500;line-height:1;white-space:nowrap}
.footer-bottom{position:absolute;top:2480px;left:0;width:1200px;height:44px;background:var(--darker);color:#888;font-size:12px;text-align:center;line-height:44px}
</style>
</head>
<body>

<header class="site-header">
  <div class="brand"><span class="brand-mark"></span>Harlow &amp; Finch</div>
  <nav class="main-nav">
    <a class="active" href="#">Home</a>
    <a href="#">About Us</a>
    <a href="#">Products</a>
    <a href="#">Blog</a>
    <a href="#">Contact Us</a>
  </nav>
  <div class="header-contact">
    <div><svg width="12" height="12" viewBox="0 0 24 24"><path fill="#fff" d="M6.6 10.8a15 15 0 0 0 6.6 6.6l2.2-2.2c.3-.3.7-.4 1-.2 1.1.4 2.3.6 3.6.6.6 0 1 .4 1 1V20c0 .6-.4 1-1 1A17 17 0 0 1 3 4c0-.6.4-1 1-1h3.5c.6 0 1 .4 1 1 0 1.3.2 2.5.6 3.6.1.3 0 .7-.2 1z"/></svg>+61 3 9555 0142</div>
    <div><svg width="12" height="12" viewBox="0 0 24 24"><path fill="#fff" d="M2 5h20v14H2zm2 2v.5l8 5 8-5V7l-8 5z"/></svg>info@harlowfinch.com</div>
  </div>
</header>

<section class="hero" role="img" aria-label="Brightly lit underground car park with LED ceiling lighting">
  <div class="hero-box">
    <h2 class="heading">Quality Services and Products</h2>
    <p>Aenean sollicitudin, lorem quis bibendum auctor, nisi elit consequat ipsum, nec sagittis sem nibh id elit amet.</p>
    <a class="btn btn-outline" href="#">Contact Us Now</a>
  </div>
  <div class="slider-dots"><span class="on"></span><span></span><span></span><span></span></div>
</section>

<section class="panel welcome">
  <div class="eyebrow heading">Welcome to</div>
  <h1 class="heading">The Commercial Lighting Division of Harlow &amp; Finch Business Solutions.</h1>
  <p>Retrofitting the lighting in a commercial or industrial premises is a great way to save money on energy costs and maintenance. Harlow &amp; Finch work alongside owners and managers to plan a better lit building that runs for less every single year.</p>
  <p>We make it all easy to access by providing you with:</p>
  <ul>
    <li>The best range of energy saving commercial and industrial lighting</li>
    <li>High quality products from reputable manufacturers that meet Australian Standards</li>
    <li>Assistance to ensure you choose the right product for the right application</li>
  </ul>
  <a class="btn btn-text" href="#">Read More</a>
</section>

<section class="panel solutions">
  <h2 class="section-title heading">We Provide These Lighting Solutions</h2>
  <span class="view-all heading">View All ›</span>
  <div class="cards">
    <article class="card">
      <h3 class="heading">Car Park Lighting</h3>
      <div class="card-img" role="img" aria-label="Car park lit by bright ceiling fittings" style="background:linear-gradient(180deg,#8f9aa0,#dfe3e4 60%,#a7aeb1)"></div>
      <p>Aenean sollicitudin, lorem quis bibendum auctor, nisi elit consequat ipsum, nec sagittis sem nibh id elit.</p>
      <a class="btn btn-red" href="#">Read More</a>
    </article>
    <article class="card">
      <h3 class="heading">Educational Lighting</h3>
      <div class="card-img" role="img" aria-label="Classroom with desks under panel lighting" style="background:linear-gradient(180deg,#e6ddc8,#b99a6e 60%,#7a5f3e)"></div>
      <p>Aenean sollicitudin, lorem quis bibendum auctor, nisi elit consequat ipsum, nec sagittis sem nibh id elit.</p>
      <a class="btn btn-red" href="#">Read More</a>
    </article>
    <article class="card">
      <h3 class="heading">Hospitality Lighting</h3>
      <div class="card-img" role="img" aria-label="Hotel lobby with warm lighting" style="background:linear-gradient(180deg,#cfd8e0,#8ea4b6 55%,#5a6d7c)"></div>
      <p>Aenean sollicitudin, lorem quis bibendum auctor, nisi elit consequat ipsum, nec sagittis sem nibh id elit.</p>
      <a class="btn btn-red" href="#">Read More</a>
    </article>
  </div>
</section>

<section class="panel media-row">
  <div class="media-col">
    <h2 class="heading">Video</h2>
    <div class="video" role="img" aria-label="Video still of a lit tunnel">
      <div class="video-bar">
        <svg width="14" height="14" viewBox="0 0 14 14"><path d="M2 1l11 6-11 6z" fill="#fff"/></svg>
        <div class="video-track"></div>
        <span style="color:#fff;font-size:11px">0:42</span>
      </div>
    </div>
  </div>
  <div class="media-col">
    <h2 class="heading">Recent Blog</h2>
    <article class="post">
      <div class="post-img" role="img" aria-label="Blog photo of a lit conference room" style="background:linear-gradient(180deg,#d9dde0,#8c969c)"><span class="date-tag">12 APR</span></div>
      <div>
        <h3 class="heading">Lorem Ipsum, Proin Ida</h3>
        <p>Lorem ipsum dolor sit amet, gravida nibh vel velit auctor aliquet aenean sollicitudin, lorem quis bibendum auctor nisi elit.</p>
      </div>
    </article>
    <article class="post">
      <div class="post-img" role="img" aria-label="Blog photo of an office ceiling with lights" style="background:linear-gradient(180deg,#2f3a44,#9aa8b3)"><span class="date-tag">08 APR</span></div>
      <div>
        <h3 class="heading">Nibh Vel Velit Auctor</h3>
        <p>Lorem ipsum dolor sit amet, gravida nibh vel velit auctor aliquet aenean sollicitudin, lorem quis bibendum auctor nisi elit.</p>
      </div>
    </article>
  </div>
</section>

<footer class="site-footer">
  <div class="footer-col" style="width:150px">
    <h4>Welcome</h4>
    <ul><li>Home</li><li>About Us</li><li>Client Notes</li><li>Services</li><li>Support</li><li>Events</li><li>Contact Us</li></ul>
  </div>
  <div class="footer-col" style="width:160px">
    <h4>Information</h4>
    <ul><li>Terms &amp; Conditions</li><li>Privacy Policy</li><li>Disclaimer</li><li>Sitemap</li></ul>
  </div>
  <div class="footer-col" style="width:220px">
    <h4>Contact Info</h4>
    <ul><li>+61 3 9555 0142</li><li>+61 3 9555 0143</li><li>Sales: sales@harlowfinch.com</li><li>Support: help@harlowfinch.com</li></ul>
  </div>
  <div class="footer-col social" style="width:150px">
    <h4>Follow Us</h4>
    <ul><li><span class="dot"></span>Friendloop</li><li><span class="dot"></span>Workmesh</li><li><span class="dot"></span>Pinboardly</li></ul>
  </div>
  <div class="footer-col" style="width:250px">
    <h4>Accepted Payments</h4>
    <div class="payments"><span></span><span></span><span></span><span></span><span></span></div>
    <div class="care">
      <svg width="34" height="34" viewBox="0 0 24 24"><path fill="#fff" d="M6.6 10.8a15 15 0 0 0 6.6 6.6l2.2-2.2c.3-.3.7-.4 1-.2 1.1.4 2.3.6 3.6.6.6 0 1 .4 1 1V20c0 .6-.4 1-1 1A17 17 0 0 1 3 4c0-.6.4-1 1-1h3.5c.6 0 1 .4 1 1 0 1.3.2 2.5.6 3.6.1.3 0 .7-.2 1z"/></svg>
      <div><small>CUSTOMER CARE</small><strong>1300-555-014</strong></div>
    </div>
  </div>
</footer>
<div class="footer-bottom">Harlow &amp; Finch Business Solutions © 2015. All rights reserved.</div>

</body>
</html>
```